Harrow Tavern & Grille Menu Makeover

I am looking for a professional look to update our current menu. We are an independently owned sports bar and grill. Up to this point, I have done all of my own graphic designing. I am looking for something classy/family oriented. We are a very family friendly sports bar that offers a wide variety of menu options. Our website is www.harrowtavernco.example. This may help you get more of a feel for what type of place we are and what we offer. Our menu is listed on the website. My current menu is 8.5x14 inserts that feature a cover page, 4 inside pages and a back page. I would like something a little more condensed than this. Possibly a large tri-fold menu? I am open to all new ideas. I do have some pictures on my menu now, and would like to continue using a few pictures to feature some of my items. I would like something that is in a format that gives me the option to change items and prices on my own in the future. I would also like it to feature, or inform my patrons about our technology that we offer. We offer online ordering and we are a "verified venue" with Brewvoke.( a social site for craft beer lovers).

Industry/Entity Type

Sports Bar

Requirements
Nice to have
• Nice to have some pictures, but does not have to. We do feature 9 different beers on tap. A lot of them are local craft beers from the state of Kansas. Not sure if that is something we can feature, but it is a nice talking point. All of our tables and bar are hand built. With a rich mahogany finish on all of our woodwork, some type of "woodgrain" look into the menu would be nice.

```html
<!DOCTYPE html>
<html lang="en">
<head>
<meta charset="utf-8">
<title>Harrow Tavern &amp; Grille — Entrees &amp; Sandwiches</title>
<link rel="stylesheet" href="https://fonts.googleapis.com/css2?family=Bebas+Neue&family=Libre+Baskerville:wght@700&family=Oswald:wght@300;400&display=swap">
<style>
  :root {
    --mahogany-deep: #3a1208;
    --mahogany: #6b2413;
    --mahogany-light: #8a3a1e;
    --parchment-light: #e6cf9f;
    --parchment: #cfac72;
    --parchment-dark: #9b7040;
    --ink: #1e1610;
    --ink-soft: #3b2d20;
    --rule: #2a1f16;
  }
  * { margin: 0; padding: 0; box-sizing: border-box; }
  html, body { width: 850px; height: 1200px; overflow: hidden; }
  body {
    position: relative;
    background:
      repeating-linear-gradient(90deg, rgba(0,0,0,0.10) 0 2px, transparent 2px 9px, rgba(255,255,255,0.03) 9px 11px, transparent 11px 23px),
      linear-gradient(90deg, var(--mahogany-deep), var(--mahogany) 25%, var(--mahogany-light) 50%, var(--mahogany) 75%, var(--mahogany-deep));
    font-family: "Oswald", sans-serif;
    color: var(--ink);
  }
  .menu-sheet { position: absolute; inset: 0; }
  .sheet-paper { position: absolute; left: 0; top: 0; width: 850px; height: 1200px; }
  .hero-fade {
    position: absolute; left: 330px; top: 100px; width: 450px; height: 260px;
    background: radial-gradient(ellipse at 40% 45%, rgba(150,95,50,0.45), rgba(120,80,40,0.18) 55%, transparent 75%);
  }
  .section-title {
    position: absolute; left: 94px;
    font-family: "Libre Baskerville", serif; font-weight: 700;
    font-size: 31px; letter-spacing: 0.5px; color: var(--ink);
  }
  .title-entrees { top: 166px; }
  .title-sandwiches { top: 600px; }
  .menu-column { position: absolute; width: 315px; list-style: none; }
  .col-left { left: 98px; }
  .col-right { left: 427px; }
  .entrees-list { top: 212px; }
  .sandwich-list { top: 652px; }
  .menu-item { margin-bottom: 8px; }
  .item-name {
    font-family: "Bebas Neue", sans-serif; font-size: 16px; line-height: 15px;
    letter-spacing: 0.2px; color: var(--ink);
  }
  .item-desc {
    font-family: "Oswald", sans-serif; font-weight: 300; font-size: 8.4px;
    line-height: 12px; text-transform: uppercase; color: var(--ink-soft);
  }
  .item-price {
    font-family: "Oswald", sans-serif; font-weight: 400; font-size: 7px;
    line-height: 9px; letter-spacing: 1px; color: var(--ink);
  }
  .divider { position: absolute; left: 200px; top: 576px; width: 450px; height: 16px; }
  .divider-line { position: absolute; top: 7px; height: 1.5px; width: 200px; background: var(--rule); }
  .divider-line.left { left: 0; }
  .divider-line.right { right: 0; }
  .divider-flourish {
    position: absolute; left: 209px; top: 0; width: 32px; height: 16px;
    border-radius: 50%; background: var(--rule); opacity: 0.85;
  }
</style>
</head>
<body>
<main class="menu-sheet">
  <svg class="sheet-paper" viewBox="0 0 850 1200" aria-hidden="true">
    <defs>
      <radialGradient id="paperTone" cx="50%" cy="45%" r="70%">
        <stop offset="0%" stop-color="#e8d3a5"/>
        <stop offset="55%" stop-color="#d3b27a"/>
        <stop offset="85%" stop-color="#b58a52"/>
        <stop offset="100%" stop-color="#8b5f32"/>
      </radialGradient>
    </defs>
    <polygon fill="url(#paperTone)" stroke="#6e4822" stroke-width="1.2"
      points="70,108 120,98 175,104 240,94 300,100 360,90 420,98 470,88 530,96 590,92 640,100 700,90 760,98 790,112 800,140 792,180 806,230 796,290 808,350 798,420 810,480 800,540 808,600 798,660 806,720 796,780 808,840 798,900 806,960 796,1020 804,1070 788,1100 740,1096 690,1108 640,1098 580,1110 520,1100 460,1110 400,1098 340,1108 280,1100 220,1110 160,1098 110,1106 66,1096 48,1060 58,1010 46,950 56,890 44,830 56,770 46,710 58,650 46,590 56,530 44,470 56,410 46,350 58,290 48,230 56,170 50,130"/>
  </svg>

  <div class="hero-fade" role="img" aria-label="Faded photo of a grilled dish blended into the parchment"></div>

  <h1 class="section-title title-entrees">ENTREES</h1>

  <ul class="menu-column col-left entrees-list">
    <li class="menu-item"><h2 class="item-name">Chicken Strip Basket</h2><p class="item-desc">Our classic chicken tenders served with your choice of side and dipping sauce.</p><p class="item-price">SMALL 5.99 / LARGE 8.99</p></li>
    <li class="menu-item"><h2 class="item-name">Grilled Chicken Breast Fillet</h2><p class="item-desc">A classic boneless, skinless chicken breast brushed with a bourbon peppercorn glaze.</p><p class="item-price">SMALL 7.99 / LARGE 10.99</p></li>
    <li class="menu-item"><h2 class="item-name">Blackened Tilapia</h2><p class="item-desc">8 oz. grilled tilapia filet, blackened and served with your choice of side.</p><p class="item-price">10.99</p></li>
    <li class="menu-item"><h2 class="item-name">Deep Fried Catfish</h2><p class="item-desc">Breaded and fried filets, served with tartar sauce.</p><p class="item-price">SMALL 7.99 / LARGE 10.99</p></li>
    <li class="menu-item"><h2 class="item-name">Pepper Jack Burger Steak</h2><p class="item-desc">A 12oz. ground beef patty smothered in melted pepper jack cheese and jalapeño peppers.</p><p class="item-price">SMALL 7.99 / LARGE 10.99</p></li>
    <li class="menu-item"><h2 class="item-name">St. Louie Ribs</h2><p class="item-desc">A three pound slab of slow roasted barbecue glazed ribs.</p><p class="item-price">HALF RACK 13.99 / FULL RACK 17.99</p></li>
    <li class="menu-item"><h2 class="item-name">Pork Stuffed Baked Potato</h2><p class="item-desc">Buttered and salted baked potato stuffed with a mountain of BBQ pulled pork, cheddar and jack cheese, blooming onion petals, sour cream and green onions. Served with a side salad</p><p class="item-price">8.99</p></li>
  </ul>

  <ul class="menu-column col-right entrees-list">
    <li class="menu-item"><h2 class="item-name">Harrow Loaded Chicken</h2><p class="item-desc">Our grilled chicken breast piled high with melted jack and cheddar cheese, sauteed onions and mushrooms, crisp bacon, and honey mustard.</p><p class="item-price">SMALL 9.99 / LARGE 12.99</p></li>
    <li class="menu-item"><h2 class="item-name">Chicken Fried Chicken Dinner</h2><p class="item-desc">Crispy chicken breast smothered in country gravy served with your choice of side and steamed vegetables.</p><p class="item-price">9.99</p></li>
    <li class="menu-item"><h2 class="item-name">Fried Shrimp</h2><p class="item-desc">A plate full of lightly breaded butterflied shrimp served with cocktail sauce.</p><p class="item-price">SMALL 7.99 / LARGE 10.99</p></li>
    <li class="menu-item"><h2 class="item-name">Country Fried Steak</h2><p class="item-desc">Hand breaded and deep fried, smothered in old fashioned country gravy.</p><p class="item-price">SMALL 7.99 / LARGE 10.99</p></li>
    <li class="menu-item"><h2 class="item-name">Black N' Blue Sirloin</h2><p class="item-desc">12 oz. choice cut sirloin cooked to your request, blackened and topped with melted blue cheese crumbles.</p><p class="item-price">15.99</p></li>
    <li class="menu-item"><h2 class="item-name">Iron Griddle Steak</h2><p class="item-desc">12 oz. aged and cut from the strip loin. Cooked to your request.</p><p class="item-price">14.99</p></li>
    <li class="menu-item"><h2 class="item-name">Flat Iron Steak</h2><p class="item-desc">9 oz. flat iron seasoned and cooked to your request.</p><p class="item-price">16.99</p></li>
  </ul>

  <div class="divider">
    <span class="divider-line left"></span>
    <span class="divider-flourish" role="img" aria-label="Small scroll flourish ornament"></span>
    <span class="divider-line right"></span>
  </div>

  <h1 class="section-title title-sandwiches">SANDWICHES</h1>

  <ul class="menu-column col-left sandwich-list">
    <li class="menu-item"><h2 class="item-name">Harrow Club Sandwich</h2><p class="item-desc">Layers of ham, turkey, roast beef, bacon and cheese. Served with mayo on a toasted focaccia bun</p><p class="item-price">9.99</p></li>
    <li class="menu-item"><h2 class="item-name">Chicken Breast Sandwich</h2><p class="item-desc">Choice of crispy or grilled chicken breast, lettuce, tomato and pickles. Served with mayo on a toasted bun.</p><p class="item-price">7.99</p></li>
    <li class="menu-item"><h2 class="item-name">Bang Bang Turkey Wrap</h2><p class="item-desc">A grilled 12 inch tortilla stuffed with roasted turkey breast, mozzarella cheese, lettuce and our spicy bang bang sauce.</p><p class="item-price">7.99</p></li>
    <li class="menu-item"><h2 class="item-name">Roast Beef &amp; Cheddar</h2><p class="item-desc">Thinly sliced slow cooked roast beef smothered with a cheddar cheese sauces on a ciabatta bun. Served with spicy BBQ sauce.</p><p class="item-price">7.99</p></li>
    <li class="menu-item"><h2 class="item-name">B.L.T.</h2><p class="item-desc">This classic bacon, lettuce and tomato sandwich is served with mayo on your choice of white, wheat or sourdough toast.</p><p class="item-price">6.99</p></li>
    <li class="menu-item"><h2 class="item-name">Fenwick's Spicy Buffalo Chicken Sandwich</h2><p class="item-desc">Crispy fried chicken breast smothered in Fenwick's spicy buffalo sauce. Served on a ciabatta bun. Dressed with jalapeño ranch, lettuce, tomato and pickle.</p><p class="item-price">8.99</p></li>
    <li class="menu-item"><h2 class="item-name">Triple Decker Reuben</h2><p class="item-desc">Layer after layer of grilled corned beef, sauerkraut, swiss cheese and thousand island dressing. Served on toasted rye.</p><p class="item-price">7.99</p></li>
  </ul>

  <ul class="menu-column col-right sandwich-list">
    <li class="menu-item"><h2 class="item-name">Classic French Dip</h2><p class="item-desc">Thinly sliced roast beef grilled and loaded with swiss cheese and grilled onions. Served with french onion soup.</p><p class="item-price">8.99</p></li>
    <li class="menu-item"><h2 class="item-name">Crispy Chicken Bacon Ranch Wrap</h2><p class="item-desc">A 12 inch grilled tortilla stuffed with crispy chicken tenders, bacon, lettuce, tomatoes and ranch dressing.</p><p class="item-price">8.99</p></li>
    <li class="menu-item"><h2 class="item-name">Southern Style Pulled Pork</h2><p class="item-desc">Smoked pulled pork smothered in tangy barbecue sauce on a toasted hoagie. Served with cole slaw on request.</p><p class="item-price">7.99</p></li>
    <li class="menu-item"><h2 class="item-name">Chicken Fry Steak Sandwich</h2><p class="item-desc">Hand breaded chicken fried steak topped with bacon, lettuce, pickles, tomato and onion.</p><p class="item-price">7.99</p></li>
    <li class="menu-item"><h2 class="item-name">Philly Steak &amp; Cheese Sandwich</h2><p class="item-desc">Thinly sliced steak piled high with melted monterey jack cheese, grilled onions and peppers on a toasted hoagie.</p><p class="item-price">7.99</p></li>
    <li class="menu-item"><h2 class="item-name">Eight Cheese Grilled Cheese</h2><p class="item-desc">Taking this classic to the gourmet level! Eight cheeses melted thick on toasted sourdough bread.</p><p class="item-price">7.99</p></li>
    <li class="menu-item"><h2 class="item-name">Chicken Cordon Bleu Sandwich</h2><p class="item-desc">Your choice of crispy or grilled chicken breast layered with grilled ham, swiss cheese, lettuce, tomatoes and pickles. Served with mayo on a toasted bun.</p><p class="item-price">8.99</p></li>
  </ul>
</main>
</body>
</html>
```